Business card design for Brivo Engineering Tandem

We need a new business card design along with all the necessary to place an order. The company is Brivo Engineering Tandem and we recently updated our logo.

```html
<!DOCTYPE html>
<html lang="en">
<head>
<meta charset="utf-8">
<title>Brivo Engineering Tandem – Business Card</title>
<link href="https://fonts.googleapis.com/css2?family=Montserrat:wght@600&family=Poppins:wght@300;400;500&display=swap" rel="stylesheet">
<style>
  :root {
    --backdrop: #676767;
    --card-grey: #929292;
    --brand-yellow: #e1bd23;
    --white: #ffffff;
    --text-grey: #8f8f8f;
    --shadow: rgba(0,0,0,0.85);
  }
  html, body {
    margin: 0;
    padding: 0;
    overflow: hidden;
  }
  body {
    width: 1093px;
    height: 1200px;
    background: var(--backdrop);
    position: relative;
    font-family: "Poppins", sans-serif;
  }
  .card {
    position: absolute;
    left: 264px;
    width: 578px;
    height: 357px;
    overflow: hidden;
    box-shadow: 3px 3px 0 var(--shadow);
  }
  .card--front { top: 226px; background: var(--card-grey); }
  .card--back { top: 620px; background: var(--white); width: 582px; }

  .accent-panel {
    position: absolute;
    top: 0; right: 0;
    width: 170px;
    height: 100%;
    background: var(--brand-yellow);
  }

  .holder {
    position: absolute;
    left: 26px;
    top: 40px;
    color: var(--white);
  }
  .holder__name {
    font-family: "Montserrat", sans-serif;
    font-weight: 600;
    font-size: 23px;
    line-height: 1;
    margin: 0;
    letter-spacing: 0.2px;
  }
  .holder__role {
    font-size: 17px;
    font-weight: 400;
    color: var(--brand-yellow);
    margin: 2px 0 0;
    line-height: 1.1;
  }
  .rule {
    width: 31px;
    height: 1.5px;
    background: var(--brand-yellow);
    margin: 12px 0;
  }
  .contacts {
    list-style: none;
    margin: 0;
    padding: 0;
    font-size: 17px;
    font-weight: 300;
    line-height: 21px;
  }
  .contacts li {
    display: flex;
    align-items: center;
    gap: 7px;
  }
  .contacts svg { width: 15px; height: 15px; flex: none; }
  .address {
    font-size: 17px;
    font-weight: 300;
    line-height: 21px;
    margin: 0;
  }

  .brand {
    position: absolute;
    top: 158px;
    left: 0; right: 0;
    display: flex;
    justify-content: center;
    align-items: center;
    gap: 12px;
  }
  .brand__mark {
    width: 18px; height: 18px;
    background: var(--brand-yellow);
  }
  .brand__name {
    font-size: 30px;
    font-weight: 500;
    color: var(--text-grey);
    letter-spacing: 1px;
    line-height: 1;
  }
  .web-line {
    position: absolute;
    top: 290px;
    left: 0; right: 0;
    display: flex;
    justify-content: center;
    align-items: center;
    gap: 8px;
    font-size: 17px;
    font-weight: 500;
    letter-spacing: 2.5px;
    color: var(--text-grey);
  }
  .web-line .highlight { color: var(--brand-yellow); }
  .web-line__rule {
    width: 47px;
    height: 1.5px;
    background: var(--brand-yellow);
  }
</style>
</head>
<body>

<section class="card card--front">
  <div class="accent-panel"></div>
  <div class="holder">
    <h1 class="holder__name">DANIEL REYES</h1>
    <p class="holder__role">Managing Director</p>
    <div class="rule"></div>
    <ul class="contacts">
      <li>
        <svg viewBox="0 0 16 16"><path d="M3 1.5l2.5 0 1 3.5-1.6 1.2a9 9 0 0 0 4.9 4.9L11 9.5l3.5 1v2.5c0 1-1 1.5-2 1.5C6.5 14.5 1.5 9.5 1.5 3.5c0-1 .5-2 1.5-2z" fill="none" stroke="var(--brand-yellow)" stroke-width="1.5"/></svg>
        044-555 018 246
      </li>
      <li>
        <svg viewBox="0 0 16 16"><rect x="0.5" y="3" width="15" height="10" fill="var(--brand-yellow)"/><path d="M0.5 3l7.5 6 7.5-6" fill="none" stroke="var(--card-grey)" stroke-width="1.2"/></svg>
        info@brivotandem.com
      </li>
      <li>
        <svg viewBox="0 0 16 16"><g fill="none" stroke="var(--brand-yellow)" stroke-width="1.3"><circle cx="8" cy="8" r="6.8"/><ellipse cx="8" cy="8" rx="3" ry="6.8"/><path d="M1.2 8h13.6M2.5 4.5h11M2.5 11.5h11"/></g></svg>
        www.brivotandem.com
      </li>
    </ul>
    <div class="rule"></div>
    <p class="address">421, Address line goes here<br>45452,Country Name</p>
  </div>
</section>

<section class="card card--back">
  <div class="brand">
    <span class="brand__mark"></span>
    <span class="brand__name">BRIVO ENGINEERING TANDEM</span>
  </div>
  <div class="web-line">
    <span class="web-line__rule"></span>
    <span>www.<span class="highlight">brivotandem</span>.com</span>
    <span class="web-line__rule"></span>
  </div>
</section>

</body>
</html>
```